Stride Institute_TNB Brand Set Up

We need the following for a new sports academy based in Cairns, QLD Australia called Stride Institute_TNB:<br/>Digital design medium for:<br/>Business identity logo / designs<br/>Header<br/>Email signature block<br/>Website with bookings & payments <br/>Social media - Instagram, Facebook<br/><br/>Colours based on Fluoro green, black & white greys

Target Market(s)

Sports

Colors

Designer to choose colors to be used in the design.

Requirements
Must have
• Sharp professional look

```html
<!DOCTYPE html>
<html lang="en">
<head>
<meta charset="utf-8">
<title>Stride Institute_TNB – Junior Development Coaching</title>
<link href="https://fonts.googleapis.com/css2?family=Source+Sans+3:wght@400;500;600&display=swap" rel="stylesheet">
<style>
  :root {
    --green: #4c9c00;
    --forest: #012e24;
    --teal: #10b88d;
    --white: #ffffff;
    --ink: #032b22;
    --photo-sky: #eeeef0;
    --photo-grass: #4f7a2c;
  }
  html, body {
    margin: 0;
    padding: 0;
    width: 1200px;
    height: 1200px;
    overflow: hidden;
    background: var(--green);
  }
  .flyer {
    position: relative;
    width: 1200px;
    height: 1200px;
    overflow: hidden;
    font-family: "Source Sans 3", "Segoe UI", sans-serif;
    color: var(--white);
    background: var(--green);
  }
  .flyer__shapes {
    position: absolute;
    inset: 0;
  }
  .services {
    position: absolute;
    left: 0;
    width: 442px;
    top: 34px;
    margin: 0;
    text-align: center;
    font-size: 30px;
    line-height: 43.5px;
    font-weight: 400;
    letter-spacing: 0.2px;
  }
  .tagline {
    position: absolute;
    left: 55px;
    margin: 0;
    font-size: 44px;
    font-weight: 500;
    line-height: 1;
  }
  .tagline--lead { top: 261px; }
  .tagline--close { top: 478px; }
  .headline {
    position: absolute;
    left: 47px;
    top: 322px;
    margin: 0;
    font-size: 112px;
    font-weight: 400;
    line-height: 1;
    letter-spacing: 1px;
  }
  .details {
    position: absolute;
    left: 31px;
    top: 576px;
    margin: 0;
    font-size: 24px;
    line-height: 35.5px;
  }
  .cta {
    position: absolute;
    left: 45px;
    top: 742px;
    width: 288px;
    height: 63px;
    border-radius: 32px;
    background: var(--white);
    color: var(--green);
    font-size: 30px;
    display: flex;
    align-items: center;
    justify-content: center;
  }
  .website {
    position: absolute;
    left: 55px;
    top: 826px;
    margin: 0;
    font-size: 25px;
  }
  .call {
    position: absolute;
    left: 36px;
    top: 908px;
    display: flex;
    align-items: flex-start;
    gap: 10px;
  }
  .call__icon {
    width: 78px;
    height: 78px;
    margin-top: 18px;
  }
  .call__label {
    margin: 0;
    font-size: 31px;
    line-height: 1.2;
  }
  .call__number {
    margin: 2px 0 0;
    font-size: 56px;
    font-weight: 500;
    line-height: 1;
    color: var(--ink);
    letter-spacing: 0.5px;
  }
</style>
</head>
<body>
<main class="flyer">
  <svg class="flyer__shapes" width="1200" height="1200" viewBox="0 0 1200 1200">
    <defs>
      <linearGradient id="photoTone" x1="0" y1="0" x2="0" y2="1">
        <stop offset="0" stop-color="var(--photo-sky)"/>
        <stop offset="0.6" stop-color="#e4e6e6"/>
        <stop offset="0.64" stop-color="#6f9543"/>
        <stop offset="1" stop-color="var(--photo-grass)"/>
      </linearGradient>
    </defs>
    <!-- white frame behind the photo area -->
    <polygon class="photo-frame" points="586,0 1200,0 1200,1017 891,1100 418,629" fill="var(--white)"/>
    <!-- photo area -->
    <polygon class="photo-area" role="img" aria-label="Photo of a player in blue socks and black boots resting a foot on a football on grass"
             points="601,0 1200,0 1200,1004 894,1082 448,637" fill="url(#photoTone)"/>
    <!-- white accent strokes across the photo -->
    <line x1="724" y1="0" x2="593" y2="101" stroke="var(--white)" stroke-width="14"/>
    <line x1="879" y1="0" x2="1200" y2="75" stroke="var(--white)" stroke-width="18"/>
    <line x1="815" y1="1012" x2="1025" y2="1056" stroke="var(--white)" stroke-width="14"/>
    <!-- headline band -->
    <polygon class="headline-band" points="0,309 560,309 619,450 0,450" fill="var(--forest)"/>
    <polygon class="headline-accent" points="593,309 628,309 685,452 650,452" fill="var(--teal)"/>
  </svg>

  <h2 class="services">AUSTRALIAN RULES<br>FOOTBALL<br>JUNIOR DEVELOPMENT<br>PRIVATE COACHING</h2>

  <p class="tagline tagline--lead">PREPARE YOURSELF</p>
  <h1 class="headline">EVERY DAY</h1>
  <p class="tagline tagline--close">TO BE THE BEST.</p>

  <p class="details">
    REGISTER YOUR INTEREST TODAY:<br>
    EMAIL: STRIDE@STRIDETNB.COM.AU<br>
    AGES 6-16 (BOYS &amp; GIRLS)
  </p>

  <div class="cta">JOIN US</div>

  <p class="website">WWW.STRIDETNB.COM.AU</p>

  <div class="call">
    <svg class="call__icon" viewBox="0 0 80 80" aria-hidden="true">
      <circle cx="40" cy="40" r="36" fill="none" stroke="var(--white)" stroke-width="4"/>
      <path d="M33 24c-3 1-6 4-6 8 0 9 9 22 18 25 3 1 6-1 8-3l-6-7-4 2c-3-2-7-9-7-13l4-2-3-9z"
            fill="none" stroke="var(--white)" stroke-width="3" stroke-linejoin="round"/>
    </svg>
    <div class="call__text">
      <p class="call__label">CALL US TODAY</p>
      <p class="call__number">0491 570 110</p>
    </div>
  </div>
</main>
</body>
</html>
```